Volbrey Inc Business Card

Looking to get an updated business card for a Contract Machining company (www.volbreyinc.example) - looking for a clean design the portrays the technical nature of the business - colors can follow the website design and be in any combination that makes sense (red black, white, metallic or silver) - logos attached for use also. Would like space for: Name, title, business phone (555 214-3086), cell phone , website (www.volbreyinc.example) - possibly QR code could be integrated for website (designer choice), business address - 418 Harlow Bend, Marrowfield, ST 48199 (cards will be for 4 employees, I will either need to modify a template or I can provide individual information)
Target Market(s)
Aerospace, defense and medical device manufacturing companies that need machining
Industry/Entity Type
Machining for aerospace, defense, medical
Contact Information for Business Card
Name, Title, Business Phone, Cell Phone, email, business website and business address
Look and feel

```html
<!DOCTYPE html>
<html lang="en">
<head>
<meta charset="UTF-8">
<title>Volbrey Inc Business Card</title>
<link href="https://fonts.googleapis.com/css2?family=Montserrat:wght@400;500;700;800&display=swap" rel="stylesheet">
<style>
  :root {
    --backdrop: #1b1b1d;
    --card: #1f1f21;
    --card-edge: #2a2a2d;
    --silver: #d4d4d6;
    --silver-soft: #bdbdc0;
    --rule: #8e8e92;
  }
  * { box-sizing: border-box; margin: 0; padding: 0; }
  html, body {
    width: 1200px;
    height: 900px;
    overflow: hidden;
    background: var(--backdrop);
    font-family: "Montserrat", Arial, sans-serif;
  }
  .sheet {
    width: 1200px;
    height: 900px;
    display: flex;
    flex-direction: column;
    align-items: center;
    justify-content: center;
    gap: 40px;
  }
  .card {
    width: 700px;
    height: 400px;
    background: var(--card);
    border: 1px solid var(--card-edge);
    box-shadow: 0 14px 34px rgba(0,0,0,0.55);
    position: relative;
  }

  /* Front */
  .card-front {
    display: flex;
    flex-direction: column;
    align-items: center;
    justify-content: center;
    gap: 20px;
  }
  .brand-disc {
    width: 140px;
    height: 140px;
    border-radius: 50%;
    background: var(--silver);
  }
  .brand-name {
    color: var(--silver);
    font-weight: 800;
    font-size: 32px;
    letter-spacing: 1px;
    text-transform: uppercase;
    line-height: 1;
    white-space: nowrap;
  }

  /* Back */
  .card-back {
    display: flex;
    align-items: center;
    padding: 0 40px 0 44px;
  }
  .back-brand {
    width: 290px;
    display: flex;
    justify-content: center;
  }
  .back-brand .brand-name { font-size: 38px; }
  .divider {
    width: 2px;
    height: 210px;
    background: var(--rule);
    margin: 0 26px 0 24px;
    flex: none;
  }
  .contact {
    color: var(--silver-soft);
    font-size: 16px;
    line-height: 1.4;
    white-space: nowrap;
  }
  .person-name {
    color: var(--silver);
    font-weight: 700;
    font-size: 23px;
    letter-spacing: 1px;
    text-transform: uppercase;
    line-height: 1.2;
  }
  .person-title {
    font-weight: 500;
    font-size: 15px;
    letter-spacing: 1px;
    text-transform: uppercase;
    margin-bottom: 10px;
  }
  .address { margin-bottom: 6px; }
  .contact-line {
    display: flex;
    align-items: center;
    gap: 8px;
  }
  .contact-line svg {
    width: 12px;
    height: 12px;
    flex: none;
    fill: none;
    stroke: var(--silver-soft);
    stroke-width: 1.6;
  }
</style>
</head>
<body>
<main class="sheet">
  <section class="card card-front">
    <div class="brand-disc"></div>
    <div class="brand-name">Volbrey Inc</div>
  </section>

  <section class="card card-back">
    <div class="back-brand">
      <div class="brand-name">Volbrey Inc</div>
    </div>
    <div class="divider"></div>
    <div class="contact">
      <div class="person-name">Darren Hollis</div>
      <div class="person-title">Director</div>
      <div class="address">418 Harlow Bend,<br>Marrowfield, ST 48199</div>
      <div class="contact-line">
        <svg viewBox="0 0 12 12"><path d="M2.5 1.5l2 .2.8 2.3-1.2 1a6 6 0 0 0 2.9 2.9l1-1.2 2.3.8.2 2A1 1 0 0 1 9.5 10.5 8.5 8.5 0 0 1 1.5 2.5a1 1 0 0 1 1-1z"/></svg>
        <span>555 214-3086</span>
      </div>
      <div class="contact-line">
        <svg viewBox="0 0 12 12"><rect x="3" y="1" width="6" height="10" rx="1"/><line x1="5.3" y1="9" x2="6.7" y2="9"/></svg>
        <span>555 407-2291</span>
      </div>
      <div class="contact-line">
        <svg viewBox="0 0 12 12"><rect x="1" y="2.5" width="10" height="7"/><path d="M1 2.5l5 4 5-4"/></svg>
        <span>info@volbreyinc.example</span>
      </div>
      <div class="contact-line">
        <svg viewBox="0 0 12 12"><circle cx="6" cy="6" r="5"/><ellipse cx="6" cy="6" rx="2.2" ry="5"/><line x1="1" y1="6" x2="11" y2="6"/></svg>
        <span>www.volbreyinc.example</span>
      </div>
    </div>
  </section>
</main>
</body>
</html>
```